Business Card Design for Technology Company

New business card design needed for technology company director.
Ideally, the design will fit the style and nature of the industry. We are a supplier of quality products and services, and we hope the design will give customers and suppliers this impression.

Target Market(s)

3D Printing Industry

Industry/Entity Type

Technology Equipment

Contact Information for Business Card

Name: Marcus Lin
Title: Director
Company address: Factory K4, 7B Harlowe Road, Springvale Victoria Australia 3150
Telephone: +61-3-8555 6413
Email: marcus.lin@vortalmake.com.au
Website: www.vortalmake.com.au

Requirements
Must have
• All information in business card details
• Company logo
• '3D Printers and 3D Print Filaments' at proper place
Nice to have
• Style to fit the industry
• Colour to fit logo

```html
<!DOCTYPE html>
<html lang="en">
<head>
<meta charset="utf-8">
<title>Vortalmake Business Card</title>
<link href="https://fonts.googleapis.com/css2?family=Roboto:wght@400;500;700&display=swap" rel="stylesheet">
<style>
  :root {
    --page-bg: #d9d9d9;
    --blue-deep: #063f72;
    --blue-mid: #0a5d9c;
    --blue-glow: #1277bd;
    --orange: #f7941d;
    --panel-white: #ffffff;
    --panel-tint: #eef3f8;
    --ink: #111111;
    --back-black: #000000;
    --text-light: #ffffff;
  }
  * { margin: 0; padding: 0; box-sizing: border-box; }
  html, body {
    width: 1125px; height: 1200px; overflow: hidden;
    background: var(--page-bg);
    font-family: "Roboto", Arial, sans-serif;
  }
  .canvas { position: relative; width: 1125px; height: 1200px; }
  .card {
    position: absolute; left: 156px; width: 826px; height: 472px; overflow: hidden;
  }
  .card-front {
    top: 106px;
    background: radial-gradient(ellipse 60% 75% at 32% 50%, var(--blue-glow) 0%, var(--blue-mid) 45%, var(--blue-deep) 100%);
  }
  .card-back { top: 639px; background: var(--back-black); }

  .hex-panel { position: absolute; inset: 0; }

  .contact { position: absolute; left: 41px; top: 84px; color: var(--text-light); }
  .person-name { font-size: 30px; font-weight: 700; letter-spacing: 0.3px; line-height: 1; }
  .person-title { font-size: 20px; font-weight: 500; margin-top: 6px; line-height: 1; }
  .address { margin-top: 48px; font-size: 19px; line-height: 25px; font-weight: 400; }
  .details { list-style: none; margin-top: 14px; font-size: 19px; line-height: 26px; }
  .details li { display: flex; align-items: center; gap: 10px; }
  .details svg { width: 18px; height: 18px; flex: none; fill: var(--text-light); }

  .brand {
    position: absolute; display: flex; align-items: center; gap: 14px;
    font-weight: 700; letter-spacing: 3px;
  }
  .brand-front { left: 432px; top: 180px; color: var(--ink); font-size: 40px; }
  .brand-front .brand-square { width: 44px; height: 44px; background: var(--orange); }
  .brand-back {
    left: 0; right: 0; top: 168px; justify-content: center;
    color: var(--orange); font-size: 44px;
  }
  .brand-back .brand-square { width: 50px; height: 50px; background: var(--blue-glow); }

  .tagline {
    position: absolute; left: 0; right: 0; top: 402px; text-align: center;
    color: var(--text-light); font-size: 20px; font-weight: 400;
  }
</style>
</head>
<body>
<main class="canvas">
  <section class="card card-front">
    <svg class="hex-panel" width="826" height="472" viewBox="0 0 826 472" aria-hidden="true">
      <defs>
        <linearGradient id="panelFade" x1="0" y1="0" x2="1" y2="1">
          <stop offset="0" stop-color="var(--panel-tint)"/>
          <stop offset="1" stop-color="var(--panel-white)"/>
        </linearGradient>
      </defs>
      <polygon points="582,0 826,0 826,472 579,472 367,358 367,118" fill="url(#panelFade)"/>
      <polyline points="582,0 367,118 367,358 579,472" fill="none" stroke="var(--orange)" stroke-width="4"/>
    </svg>

    <div class="contact">
      <h1 class="person-name">MARCUS LIN</h1>
      <p class="person-title">DIRECTOR</p>
      <p class="address">Factory K4, 7B<br>Harlowe Road, Springvale<br>Victoria, Australia 3150</p>
      <ul class="details">
        <li><svg viewBox="0 0 24 24"><path d="M6.6 10.8a15.1 15.1 0 0 0 6.6 6.6l2.2-2.2c.3-.3.7-.4 1-.2 1.1.4 2.3.6 3.6.6.6 0 1 .4 1 1V20c0 .6-.4 1-1 1C10.6 21 3 13.4 3 4c0-.6.4-1 1-1h3.5c.6 0 1 .4 1 1 0 1.3.2 2.5.6 3.6.1.3 0 .7-.2 1z"/></svg>+61-3-8555 6413</li>
        <li><svg viewBox="0 0 24 24"><path d="M2 5h20v14H2z M4 7v.5l8 5 8-5V7l-8 5z" fill-rule="evenodd"/></svg>marcus.lin@vortalmake.com.au</li>
        <li><svg viewBox="0 0 24 24"><path d="M12 2a10 10 0 1 0 0 20 10 10 0 0 0 0-20zm-1 17.9A8 8 0 0 1 4.1 10L9 15v1a2 2 0 0 0 2 2zm6.9-2.5A2 2 0 0 0 16 16h-1v-3a1 1 0 0 0-1-1H8v-2h2a1 1 0 0 0 1-1V7h2a2 2 0 0 0 2-2v-.4a8 8 0 0 1 2.9 12.8z"/></svg>www.vortalmake.com.au</li>
      </ul>
    </div>

    <div class="brand brand-front"><span class="brand-square"></span><span class="brand-name">VORTALMAKE</span></div>
  </section>

  <section class="card card-back">
    <div class="brand brand-back"><span class="brand-square"></span><span class="brand-name">VORTALMAKE</span></div>
    <p class="tagline">3D Printers and 3D Print Filaments</p>
  </section>
</main>
</body>
</html>
```